Corvane Capital Business Cards

These are professional business cards that are for my family office.
Put fake emails and phone numbers as of now until I finalize those components. This family office controls my families investments, assets, and future. The cards should be professional.
..
.
.
.
I just uploaded another variation of a logo I would like to see as a business card to I am inbeteen which logo to use

Target Market(s)

business

Industry/Entity Type

business

Contact Information for Business Card

Professional, wealth related, finance related.

Requirements
Must have
• Logo

```html
<!DOCTYPE html>
<html lang="en">
<head>
<meta charset="utf-8">
<title>Corvane Capital Business Cards</title>
<link rel="stylesheet" href="https://fonts.googleapis.com/css2?family=Cinzel:wght@500;700&family=Arimo:wght@400&display=swap">
<style>
  :root {
    --stage: #2b2c2f;
    --navy: #1b1f2b;
    --paper: #ffffff;
    --ink: #1b1f2b;
    --muted: #8a8c90;
    --band-grey: #a6a7aa;
    --rule: #c9cacd;
  }
  * { box-sizing: border-box; margin: 0; padding: 0; }
  html, body {
    width: 1200px; height: 874px; overflow: hidden;
    background: var(--stage);
  }
  .stage {
    width: 1200px; height: 874px;
    display: flex; flex-direction: column;
    align-items: center; justify-content: center; gap: 44px;
  }
  .card {
    position: relative;
    width: 600px; height: 343px;
    border-radius: 18px;
    overflow: hidden;
    box-shadow: 0 10px 30px rgba(0,0,0,0.45);
  }
  /* Front */
  .card-front { background: var(--navy); color: var(--paper); }
  .front-mark {
    position: absolute; left: 0; right: 0; top: 120px;
    display: flex; align-items: center; justify-content: center; gap: 16px;
  }
  .mark-ring {
    width: 26px; height: 26px; border: 2px solid var(--paper); border-radius: 50%;
  }
  .brand-name {
    font-family: "Cinzel", serif; font-weight: 500;
    font-size: 34px; letter-spacing: 1px;
  }
  .front-url {
    position: absolute; left: 0; right: 0; bottom: 34px; text-align: center;
    font-family: "Arimo", sans-serif; font-size: 15px; letter-spacing: 3px;
  }
  /* Back */
  .card-back { background: var(--paper); color: var(--ink); }
  .back-brand {
    position: absolute; left: 0; width: 270px; top: 62px;
    display: flex; flex-direction: column; align-items: center; gap: 16px;
  }
  .back-brand .mark-ring { width: 74px; height: 74px; border-color: var(--ink); }
  .back-brand .brand-name { font-size: 25px; color: var(--ink); }
  .divider {
    position: absolute; left: 282px; top: 40px; width: 1px; height: 170px;
    background: var(--rule);
  }
  .contact { position: absolute; left: 304px; top: 44px; font-family: "Arimo", sans-serif; }
  .person-name {
    font-family: "Cinzel", serif; font-weight: 700; font-size: 25px; letter-spacing: 0.5px;
  }
  .person-title { font-size: 13px; color: var(--muted); margin-top: -2px; }
  .address { font-size: 15px; line-height: 19px; margin-top: 14px; }
  .lines { list-style: none; margin-top: 6px; font-size: 15px; line-height: 19px; }
  .lines li { display: flex; align-items: center; gap: 10px; }
  .lines svg { width: 12px; height: 12px; flex: none; }
  .bands { position: absolute; left: 0; bottom: 0; width: 600px; height: 130px; }
  .back-url {
    position: absolute; right: 26px; bottom: 24px;
    font-family: "Arimo", sans-serif; font-size: 16px; color: var(--paper);
  }
</style>
</head>
<body>
<main class="stage">
  <section class="card card-front">
    <div class="front-mark">
      <span class="mark-ring"></span>
      <span class="brand-name">Corvane Capital</span>
    </div>
    <p class="front-url">www.corvanecapital.com</p>
  </section>

  <section class="card card-back">
    <div class="back-brand">
      <span class="mark-ring"></span>
      <span class="brand-name">Corvane Capital</span>
    </div>
    <div class="divider"></div>
    <div class="contact">
      <h1 class="person-name">Daniel Hart</h1>
      <p class="person-title">President</p>
      <p class="address">4120 Alder Court<br>Halden, Canada 21908</p>
      <ul class="lines">
        <li><svg viewBox="0 0 12 12"><path d="M2 1l2 0 1 3-1.5 1a6 6 0 0 0 3.5 3.5L8 7l3 1 0 2a1 1 0 0 1-1 1A9 9 0 0 1 1 2a1 1 0 0 1 1-1z" fill="#1b1f2b"/></svg>555-204-7316</li>
        <li><svg viewBox="0 0 12 12"><rect x="3" y="0.5" width="6" height="11" rx="1" fill="none" stroke="#1b1f2b"/><circle cx="6" cy="9.5" r="0.7" fill="#1b1f2b"/></svg>555-318-6042</li>
        <li><svg viewBox="0 0 12 12"><rect x="0.5" y="2" width="11" height="8" fill="#1b1f2b"/><path d="M0.5 2l5.5 4.5L11.5 2" fill="none" stroke="#fff"/></svg>info@corvanecapital.com</li>
      </ul>
    </div>
    <svg class="bands" viewBox="0 0 600 130" preserveAspectRatio="none">
      <path d="M0 22 H266 Q272 22 276 28 L282 36 H0 Z" fill="var(--band-grey)"/>
      <path d="M0 36 H282 Q288 36 292 44 L296 52 Q299 58 306 58 H600 V130 H0 Z" fill="var(--navy)"/>
      <path d="M0 40 H0" fill="none"/>
    </svg>
    <p class="back-url">www.corvanecapital.com</p>
  </section>
</main>
</body>
</html>
```